Business Card Design

I'm a commercial general contractor remodel offices, hotels, health clubs and stores mostly San Francisco and the peninsula
the file I down loaded is kind of what I want I like the I beam with my company name in it, that would be fine with me but if you have better Idea will look at it you never know, I'm decided to give in and change my company name to how every one knows me, I have been in business since 1991, I like the I beam logo I included one of my old card from my old company for reference for you.

BROCK CONSTRUCTION (is my company name)
Warren Pelkey contractor, LIc 514387
3148 Larkspur Row, San Bruno, California 94071
mobile, (415) 736-4052
phone (650) 514-2087
Fax, (650) 514-2088
email, brock@brockconstruction.example

```html
<!DOCTYPE html>
<html lang="en">
<head>
<meta charset="utf-8">
<title>Brock Construction – Business Card</title>
<link rel="stylesheet" href="https://fonts.googleapis.com/css2?family=Lato:wght@400;700&display=swap">
<style>
  :root {
    --backdrop: #3a322d;
    --card: #141414;
    --card-edge: #222;
    --accent: #2a8fd6;
    --text: #f2f2f2;
    --silver: #c9c9c9;
    --divider: #2c2c2c;
  }
  * { box-sizing: border-box; margin: 0; padding: 0; }
  html, body { width: 1200px; height: 844px; overflow: hidden; }
  body {
    background: var(--backdrop);
    font-family: "Lato", sans-serif;
    position: relative;
  }
  .card {
    position: absolute;
    top: 272px;
    width: 525px;
    height: 300px;
    background: var(--card);
    border: 1px solid var(--card-edge);
    box-shadow: 0 12px 30px rgba(0,0,0,.45);
  }
  .card--front { left: 50px; }
  .card--back { left: 625px; }

  .brand {
    position: absolute;
    font-weight: 700;
    letter-spacing: 0.06em;
    line-height: 1.1;
    text-transform: uppercase;
  }
  .card--front .brand {
    left: 30px;
    top: 128px;
    width: 190px;
    font-size: 22px;
    color: var(--accent);
  }
  .card--back .brand {
    left: 0; right: 0;
    top: 122px;
    text-align: center;
    font-size: 30px;
    color: var(--silver);
  }

  .contact {
    position: absolute;
    left: 240px;
    top: 42px;
    padding-left: 14px;
    border-left: 1px solid var(--divider);
    color: var(--text);
    font-size: 14px;
    line-height: 1.3;
  }
  .contact__name {
    color: var(--accent);
    font-size: 21px;
    margin-bottom: 2px;
  }
  .contact__address { margin-top: 10px; }
  .contact__lines { list-style: none; margin-top: 14px; }
  .contact__label { color: var(--accent); display: inline-block; width: 18px; }
</style>
</head>
<body>
  <section class="card card--front">
    <div class="brand">Brock<br>Construction</div>
    <div class="contact">
      <p class="contact__name">Warren Pelkey</p>
      <p>Contractor</p>
      <p>Lic 514387</p>
      <p class="contact__address">3148 Larkspur Row, San Bruno,<br>California 94071</p>
      <ul class="contact__lines">
        <li><span class="contact__label">T:</span>(415) 736-4052</li>
        <li><span class="contact__label">P:</span>(650) 514-2087</li>
        <li><span class="contact__label">F:</span>(650) 514-2088</li>
        <li><span class="contact__label">E:</span>brock@brockconstruction.example</li>
      </ul>
    </div>
  </section>

  <section class="card card--back">
    <div class="brand">Brock Construction</div>
  </section>
</body>
</html>
```